Business Card design for insurance broker in Denver, CO, USA

I need a business card designed using this logo that was just created. We sell life and disability income insurance to US consumers.
Looking for a professionally designed card to make use of the logo and have something to hand to prospects or new business referral sources. The card could be white, gray, black or whatever you would recommend.

Target Market(s)

US Consumers and other financial professionals that I partner with.

Industry/Entity Type

Insurance Broker

Contact Information for Business Card

Owen T. Farrow, KRA, QBLP (please note that KRA should have a superscript R in a circle for registered trademark)
President
phone (303) 555-0187
email owen@keelbrookcover.example
4620 W. Halvern Rd, Suite 300, Larkmoor Springs, CO 80499
Somewhere fit in a tagline saying "Your resource for life, long term care, and disability insurance" (maybe the back if it doesn't fit on the front, your call)

Font styles to use
Sans Serif

Requirements
Must have
• Must have logo in correct blue and gray colors, my name, address, phone, email. Order and placement determined by the designer.
• I just want something that looks a more professional than what I could have done using the business card designer tool on pixelbazaar.example or QuillPress, or any other do-it-yourself tool
• A regular rectangular business card with square corners is preferred
Nice to have
• I included the logos of 2 organizations I belong to (GKLS and WOBCE). They should be small, but visible on the back only. If it doesn’t look good, this is not a requirement, feel free to drop it.
Should not have
• Do not add any colors not already in the logo, except use of black and whites which are okay. If you use the logo on the back and want to make that in all black, gray or white, that may be okay as well.

```html
<!DOCTYPE html>
<html lang="en">
<head>
<meta charset="utf-8">
<title>Keelbrook Cover — Business Card</title>
<link rel="stylesheet" href="https://fonts.googleapis.com/css2?family=Montserrat:wght@600&family=Open+Sans:wght@400;600&display=swap">
<style>
  :root {
    --brand-blue: #1f7fd0;
    --brand-gray: #8f8f8f;
    --card-gray: #a4a4a4;
    --badge-gray: #8a8a8a;
    --ink: #3a3a3a;
    --white: #ffffff;
    --backdrop: #1c1c1c;
  }
  * { box-sizing: border-box; margin: 0; padding: 0; }
  html, body { width: 1200px; height: 900px; overflow: hidden; background: var(--backdrop); }
  body { font-family: "Open Sans", sans-serif; position: relative; }

  .card { position: absolute; left: 320px; width: 560px; height: 320px; overflow: hidden; }
  .card--back { top: 100px; background: var(--card-gray); }
  .card--front { top: 480px; background: var(--white); }

  /* wordmark */
  .wordmark { position: absolute; display: flex; align-items: center; gap: 14px; }
  .wordmark__dot { width: 24px; height: 24px; border-radius: 50%; background: var(--brand-blue); flex: none; }
  .wordmark__name {
    font-family: "Montserrat", sans-serif; font-weight: 600; font-size: 30px;
    letter-spacing: 1px; text-transform: uppercase; line-height: 1.05;
  }
  .card--back .wordmark { left: 170px; top: 72px; }
  .card--back .wordmark__name { color: var(--white); }
  .card--front .wordmark { left: 170px; top: 112px; }
  .card--front .wordmark__name { color: var(--brand-blue); }

  /* back card */
  .memberships { position: absolute; left: 300px; top: 160px; display: flex; gap: 22px; }
  .badge { width: 44px; height: 34px; background: var(--badge-gray); }
  .tagline {
    position: absolute; left: 0; right: 0; bottom: 44px; text-align: center;
    color: var(--white); font-size: 14px; letter-spacing: .3px;
  }

  /* front card */
  .edge-bar { position: absolute; width: 8px; }
  .edge-bar--name { left: 0; top: 40px; height: 42px; background: var(--brand-blue); }
  .edge-bar--address { right: 0; top: 146px; height: 48px; background: var(--brand-blue); }
  .edge-bar--contact { left: 0; bottom: 22px; height: 60px; background: #b5b5b5; }

  .person { position: absolute; left: 28px; top: 38px; }
  .person__name { font-family: "Montserrat", sans-serif; font-weight: 600; font-size: 19px; color: var(--brand-blue); text-transform: uppercase; }
  .person__creds { color: var(--brand-gray); }
  .person__creds sup { font-size: 10px; }
  .person__title { font-size: 13px; color: var(--ink); margin-top: 1px; }

  .address { position: absolute; right: 28px; top: 146px; text-align: right; font-size: 12.5px; line-height: 1.45; color: var(--ink); font-style: normal; }

  .contact { position: absolute; left: 28px; bottom: 22px; list-style: none; font-size: 13px; color: var(--ink); line-height: 1.55; }
  .contact li { display: flex; align-items: center; gap: 8px; }
  .contact svg { width: 14px; height: 14px; flex: none; }
</style>
</head>
<body>

<section class="card card--back" aria-label="Card back">
  <div class="wordmark"><span class="wordmark__dot"></span><span class="wordmark__name">Keelbrook<br>Cover</span></div>
  <div class="memberships">
    <span class="badge" role="img" aria-label="Membership badge"></span>
    <span class="badge" role="img" aria-label="Association badge"></span>
  </div>
  <p class="tagline">"Your resource for life, long term care, and disability insurance"</p>
</section>

<section class="card card--front" aria-label="Card front">
  <span class="edge-bar edge-bar--name"></span>
  <span class="edge-bar edge-bar--address"></span>
  <span class="edge-bar edge-bar--contact"></span>

  <div class="person">
    <p class="person__name">Owen T. Farrow, <span class="person__creds">KRA<sup>®</sup> , QBLP</span></p>
    <p class="person__title">President</p>
  </div>

  <div class="wordmark"><span class="wordmark__dot"></span><span class="wordmark__name">Keelbrook<br>Cover</span></div>

  <address class="address">
    4620 W. Halvern Rd<br>
    Suite 300, Larkmoor Springs<br>
    CO 80499
  </address>

  <ul class="contact">
    <li><svg viewBox="0 0 14 14"><circle cx="7" cy="7" r="7" fill="#1f7fd0"/><path d="M4.5 3.5l1.5 0.3 0.4 1.7-0.9 0.7a5 5 0 0 0 2.3 2.3l0.7-0.9 1.7 0.4 0.3 1.5c-3.4 0.6-6.6-2.6-6-6z" fill="#fff"/></svg>(303) 555-0187</li>
    <li><svg viewBox="0 0 14 14"><circle cx="7" cy="7" r="7" fill="#1f7fd0"/><rect x="3.5" y="4.5" width="7" height="5" fill="none" stroke="#fff"/><path d="M3.5 4.5l3.5 3 3.5-3" fill="none" stroke="#fff"/></svg>owen@keelbrookcover.example</li>
    <li><svg viewBox="0 0 14 14"><circle cx="7" cy="7" r="7" fill="#1f7fd0"/><circle cx="7" cy="7" r="3.6" fill="none" stroke="#fff"/><path d="M3.4 7h7.2M7 3.4c-1.6 2-1.6 5.2 0 7.2M7 3.4c1.6 2 1.6 5.2 0 7.2" fill="none" stroke="#fff" stroke-width=".8"/></svg>www.keelbrookcover.example</li>
  </ul>
</section>

</body>
</html>
```